Business Cards - Brightpath Horizon

need to design unique business card for my mortgage business. I need to design credit card style business card for my business or any unique idea that you might have

Target Market(s)

Home Loan customers

Industry/Entity Type

Mortgage Brokerage

Contact Information for Business Card

please design credit card style or very unique style business card

Colors

Designer to choose colors to be used in the design.

Requirements
Must have
• Name
• position
• Phone number
• fax number
• email address
• website address
• social media address
• All above fields will be provided once design in finalised

```html
<!DOCTYPE html>
<html lang="en">
<head>
<meta charset="utf-8">
<title>Brightpath Horizon — Business Card</title>
<link href="https://fonts.googleapis.com/css2?family=Work+Sans:wght@400;500;600&display=swap" rel="stylesheet">
<style>
  :root {
    --page-bg: #141414;
    --card-bg: #222222;
    --brand-blue: #2f4fb5;
    --accent-blue: #1f6fd0;
    --brand-orange: #f0901e;
    --text-light: #f2f2f2;
  }
  * { margin: 0; padding: 0; box-sizing: border-box; }
  html, body {
    width: 1200px; height: 900px; overflow: hidden;
    background: var(--page-bg);
    font-family: "Work Sans", sans-serif;
  }
  .canvas {
    position: relative; width: 1200px; height: 900px;
    display: flex; flex-direction: column; align-items: center;
    justify-content: center; gap: 30px;
  }
  .card {
    position: relative; width: 700px; height: 400px;
    background: var(--card-bg);
    box-shadow: 0 10px 30px rgba(0,0,0,.5);
  }
  .card-front {
    display: flex; flex-direction: column; align-items: center; justify-content: center;
  }
  .brand-lockup { display: flex; flex-direction: column; align-items: center; }
  .brand-name {
    display: flex; align-items: center; gap: 14px;
    color: var(--brand-blue); font-weight: 600; text-transform: uppercase;
    letter-spacing: 2px; line-height: 1; white-space: nowrap;
  }
  .brand-dot { border-radius: 50%; background: var(--brand-blue); flex: none; }
  .card-front .brand-name { font-size: 44px; }
  .card-front .brand-dot { width: 22px; height: 22px; }
  .tagline { color: var(--brand-orange); font-weight: 400; margin-top: 14px; white-space: nowrap; }
  .card-front .tagline { font-size: 22px; }

  .card-back { display: flex; align-items: center; }
  .back-brand { width: 335px; padding-left: 28px; }
  .card-back .brand-name { font-size: 23px; gap: 9px; letter-spacing: 1px; }
  .card-back .brand-dot { width: 13px; height: 13px; }
  .card-back .tagline { font-size: 16px; margin-top: 10px; }
  .divider { width: 2px; height: 230px; background: var(--brand-orange); flex: none; }
  .contact-block { padding-left: 38px; color: var(--text-light); }
  .person-name {
    color: var(--accent-blue); font-size: 24px; font-weight: 500;
    text-transform: uppercase; letter-spacing: 1px;
  }
  .person-role { font-size: 17px; text-transform: uppercase; margin-top: 2px; }
  .address { font-size: 16px; line-height: 1.4; margin-top: 20px; }
  .contact-list { list-style: none; margin-top: 18px; }
  .contact-list li {
    display: flex; align-items: center; gap: 16px;
    font-size: 17px; line-height: 1.6;
  }
  .contact-icon { width: 14px; height: 14px; flex: none; fill: var(--accent-blue); }
</style>
</head>
<body>
<main class="canvas">
  <section class="card card-front">
    <div class="brand-lockup">
      <div class="brand-name"><span class="brand-dot"></span>Brightpath Horizon</div>
      <div class="tagline">Smart choices, Solid ground</div>
    </div>
  </section>

  <section class="card card-back">
    <div class="back-brand">
      <div class="brand-lockup">
        <div class="brand-name"><span class="brand-dot"></span>Brightpath Horizon</div>
        <div class="tagline">Smart choices, Solid ground</div>
      </div>
    </div>
    <div class="divider"></div>
    <div class="contact-block">
      <div class="person-name">Daniel Reyes</div>
      <div class="person-role">Founder</div>
      <div class="address">47 Linden Crescent,<br>Oakvale ON K4R 2T9</div>
      <ul class="contact-list">
        <li>
          <svg class="contact-icon" viewBox="0 0 14 14" aria-hidden="true"><path d="M4 0h6a1 1 0 0 1 1 1v12a1 1 0 0 1-1 1H4a1 1 0 0 1-1-1V1a1 1 0 0 1 1-1zm0 2v9h6V2zm3 9.8a.7.7 0 1 0 0 1.4.7.7 0 0 0 0-1.4z"/></svg>
          (555) 310-4826
        </li>
        <li>
          <svg class="contact-icon" viewBox="0 0 14 14" aria-hidden="true"><path d="M3 0h8v4H3zM1 5h12a1 1 0 0 1 1 1v5h-3v3H3v-3H0V6a1 1 0 0 1 1-1zm3 4v4h6V9z"/></svg>
          (555) 310-4900
        </li>
        <li>
          <svg class="contact-icon" viewBox="0 0 14 14" aria-hidden="true"><path d="M0 3h14v8H0zm1 1v.4l6 3.6 6-3.6V4zm0 1.6V10h12V5.6L7 9.2z"/></svg>
          dreyes@brightpathmail.com
        </li>
        <li>
          <svg class="contact-icon" viewBox="0 0 14 14" aria-hidden="true"><path d="M7 0a7 7 0 1 1 0 14A7 7 0 0 1 7 0zm0 1.2a5.8 5.8 0 0 0-2.4 11.1V10l1.6-1.6L4.5 6.6 3 7V5l2.2-2L7 4V1.2zm2 .4V4L8 6l2 1 1.5 3.2A5.8 5.8 0 0 0 9 1.6z"/></svg>
          brightpathhomes.com
        </li>
      </ul>
    </div>
  </section>
</main>
</body>
</html>
```